Spy/Espionage/Counterintelligence Membership Community Needs a PowerPoint Template

We need a powerpoint template for one of our business verticals focused on spies, espionage, and counterintelligence. The name of it is "Brass Lantern Guild" and the logo is attached. Brass Lantern Guild is a community that connects people with experts in espionage and counterintelligence through an online social network, as well as in-person events. We would like to see designs that incorporate the red and black of the logo. The design should communicate mystery/suspense and peak curiosity.

Target Market(s)

Late 20s to baby boomers, male

Industry/Entity Type

Social Club

Font styles to use
Sans Serif

Colors
ec1f27
000000
ffffff

Requirements
Must have
• A user-friendly ppt template file. Incorporate basic fonts that don't have to be installed on every computer for presentations. A cover slide and a basic inside slide. A white background. I will also need graphic source files.
Nice to have
• Plenty of space for slide title and body content. Logo on every slide.
Should not have
• Inconsistency with fonts. Misalignment of images.

```html
<!DOCTYPE html>
<html lang="en">
<head>
<meta charset="utf-8">
<title>Brass Lantern Guild – Presentation Template</title>
<link rel="stylesheet" href="https://fonts.googleapis.com/css2?family=Figtree:wght@300;400;600;700;800&display=swap">
<style>
:root{
  --red:#d70a10;
  --red-dark:#a00006;
  --ink:#3a3a3a;
  --black:#000;
  --white:#fff;
  --paper-top:#ffffff;
  --paper-bottom:#e4e4e4;
  --rule:#b9b9b9;
  --grey-head:#a9a9a9;
  --grey-cat:#cfcfcf;
  --grey-dark:#4a4a4a;
  --grey-mid:#6a6a6a;
}
*{box-sizing:border-box;margin:0;padding:0}
html,body{width:1061px;height:1200px;overflow:hidden;background:var(--black)}
body{font-family:"Figtree",Arial,sans-serif;color:var(--ink)}
.sheet{position:absolute;left:0;top:0;width:1000px;height:1131px;transform:scale(1.061);transform-origin:0 0}
.slide{position:absolute;width:489px;height:367px;overflow:hidden;
  background:linear-gradient(180deg,var(--paper-top) 0%,var(--paper-bottom) 100%)}
.slide::before{content:"";position:absolute;left:0;top:0;right:0;height:9px;background:var(--red)}
.s1{left:8px;top:8px}.s2{left:505px;top:8px}
.s3{left:8px;top:383px}.s4{left:505px;top:383px}
.s5{left:8px;top:757px}.s6{left:505px;top:757px}
.red{color:var(--red)}
.rule{position:absolute;left:40px;right:40px;height:1px;background:var(--rule)}
.band{position:absolute;left:0;right:0;bottom:0;height:84px;background:linear-gradient(180deg,var(--red) 0%,var(--red-dark) 100%)}

/* brand mark */
.brand{position:absolute;display:flex;align-items:center;gap:6px;font-weight:400;color:var(--black);letter-spacing:-.3px;white-space:nowrap}
.brand .dot{width:36px;height:36px;border-radius:50%;background:var(--red);flex:none}

/* cover */
.cover-title{position:absolute;left:0;right:0;top:78px;text-align:center;font-weight:800;font-size:45px;line-height:1;color:var(--ink);letter-spacing:-.5px}
.cover-sub{position:absolute;left:0;right:0;top:133px;text-align:center;font-weight:400;font-size:38px;line-height:1;color:var(--ink)}
.presenter{position:absolute;right:40px;top:228px;text-align:right;font-size:12px;line-height:16px;color:var(--ink)}
.presenter strong{display:block;color:var(--red);font-size:14px;font-weight:700}
.chevron{position:absolute;left:240px;bottom:13px}

/* inside slides */
.heading{position:absolute;left:20px;top:19px;font-size:27px;font-weight:700;color:var(--ink);line-height:1}
.heading::before{content:"";position:absolute;left:-20px;top:4px;width:12px;height:19px;background:var(--red)}
.footer-rule{position:absolute;left:14px;right:14px;top:333px;height:1px;background:var(--rule)}
.footer .brand{left:20px;top:341px;font-size:17px}
.nav{position:absolute;right:36px;top:341px;display:flex;gap:4px}
.nav span{width:21px;height:19px;background:var(--red);border-radius:3px;display:flex;align-items:center;justify-content:center}
.pageno{position:absolute;right:14px;top:342px;font-size:12px;color:var(--ink);border-left:1px solid var(--rule);padding-left:10px;line-height:18px}

.about{position:absolute;left:20px;right:22px;top:65px;font-size:13.2px;line-height:18px;text-align:justify;color:var(--ink)}
.about p{margin-bottom:12px}
.about b{color:var(--red);font-weight:600}

.services{position:absolute;left:38px;top:68px;list-style:none}
.services li{font-size:17px;line-height:23.5px;position:relative;padding-left:20px;color:var(--ink)}
.services li::before{content:"";position:absolute;left:2px;top:9px;width:6px;height:6px;background:var(--red);transform:rotate(45deg)}
.team-photo{position:absolute;left:214px;top:76px;width:252px;height:216px;border-radius:4px;
  background:radial-gradient(ellipse at 50% 55%,#5a5a5a 0%,#2c2c2c 55%,rgba(0,0,0,0) 72%)}

.grid{position:absolute;left:23px;top:68px;width:442px;border-collapse:collapse;font-size:9px;table-layout:fixed}
.grid th{height:24px;font-size:13px;font-weight:700}
.grid th.cat{background:var(--grey-head);color:var(--ink)}
.grid th.o1{background:var(--red);color:var(--white)}
.grid th.o2{background:var(--grey-dark);color:var(--white)}
.grid td{height:17px;text-align:center;color:var(--white)}
.grid td.item{text-align:left;padding-left:28px;color:var(--ink);background:var(--white)}
.grid tr:nth-child(even) td.item{background:#efefef}
.grid td.yes{background:var(--red)}
.grid tr:nth-child(even) td.yes{background:#e0393e}
.grid td.no{background:var(--grey-dark)}
.grid tr:nth-child(even) td.no{background:var(--grey-mid)}
.grid tr.group td{background:var(--grey-cat);text-align:left;padding-left:5px;color:var(--ink);font-weight:700;height:17px}

.map{position:absolute;left:30px;top:70px;width:208px;height:206px;border:4px solid var(--white);box-shadow:0 0 3px rgba(0,0,0,.3);
  background:linear-gradient(160deg,#d9dcc4 0%,#c8d4a8 45%,#8fb6d6 75%,#a9c8e2 100%)}
.contact{position:absolute;left:250px;top:70px;width:222px;font-size:8.6px;line-height:10.5px;color:var(--ink)}
.contact p{text-align:justify;margin-bottom:6px}
.contact h4{color:var(--red);font-size:10.5px;font-weight:700;margin-top:5px;line-height:13px}
.social{position:absolute;left:32px;top:296px;display:flex;align-items:center;gap:6px;font-size:11px;font-weight:600;color:var(--ink)}
.social i{width:16px;height:16px;background:var(--red);border-radius:2px;display:block}
.social span{margin-left:2px}

.thanks{position:absolute;left:0;right:0;top:92px;text-align:center;font-size:64px;font-weight:800;letter-spacing:-2px;line-height:1;color:var(--ink)}
.end-brand{position:absolute;left:0;right:0;top:208px;display:flex;flex-direction:column;align-items:center;gap:4px;font-size:19px;color:var(--black)}
.end-brand .dot{width:48px;height:48px;border-radius:50%;background:var(--red)}
</style>
</head>
<body>
<main class="sheet">

  <section class="slide s1" aria-label="Cover slide">
    <div class="rule" style="top:49px"></div>
    <h1 class="cover-title"><span class="red">TITLE</span> PROJECT</h1>
    <p class="cover-sub">subtext <span class="red">presentation</span></p>
    <div class="rule" style="top:208px"></div>
    <div class="brand" style="left:44px;top:230px;font-size:19px"><span class="dot"></span>Brass Lantern Guild</div>
    <p class="presenter">Presentation by<strong>Daniel Reeve</strong></p>
    <div class="band"></div>
    <svg class="chevron" width="32" height="56" viewBox="0 0 32 56"><path d="M2 0 L32 28 L2 56 L2 44 L20 28 L2 12 Z" fill="#fff"/></svg>
  </section>

  <section class="slide s2" aria-label="About slide">
    <h2 class="heading"><span class="red">About</span> Company</h2>
    <div class="about">
      <p><b>Lorem ipsum</b> dolor sit amet, consectetuer adipiscing elit. Maecenas porttitor congue massa. Fusce posuere, magna sed pulvinar ultricies, purus lectus malesuada libero, sit amet commodo magna eros quis urna.</p>
      <p><b>Nunc viverra imperdiet enim</b>. Fusce est. Vivamus a tellus. Pellentesque habitant morbi tristique senectus et netus et malesuada fames ac turpis egestas. Proin pharetra nonummy pede. Mauris et orci.</p>
      <p><b>Aenean nec lorem.</b> In porttitor. Donec laoreet nonummy augue.</p>
      <p>Suspendisse dui purus, scelerisque at, vulputate vitae, pretium mattis, nunc. Mauris eget neque at sem venenatis eleifend. Ut nonummy.</p>
      <p><b>Fusce aliquet pede non pede.</b><br>Suspendisse dapibus lorem pellentesque magna. Integer nulla.</p>
    </div>
    <div class="footer"><div class="footer-rule"></div><div class="brand">Brass Lantern Guild</div></div>
    <div class="nav"><span><svg width="9" height="11"><path d="M7 1 L2 5.5 L7 10" stroke="#fff" stroke-width="2.4" fill="none"/></svg></span><span><svg width="9" height="11"><path d="M2 1 L7 5.5 L2 10" stroke="#fff" stroke-width="2.4" fill="none"/></svg></span></div>
    <div class="pageno">2</div>
  </section>

  <section class="slide s3" aria-label="Services slide">
    <h2 class="heading"><span class="red">Our</span> Services</h2>
    <ul class="services">
      <li>Lorem ipsum</li><li>Lorem ipsum</li><li>Lorem ipsum</li><li>Lorem ipsum</li><li>Lorem ipsum</li>
      <li>Lorem ipsum</li><li>Lorem ipsum</li><li>Lorem ipsum</li><li>Lorem ipsum</li><li>Lorem ipsum</li>
    </ul>
    <div class="team-photo" role="img" aria-label="Photo of a business team standing together"></div>
    <div class="footer"><div class="footer-rule"></div><div class="brand">Brass Lantern Guild</div></div>
    <div class="nav"><span><svg width="9" height="11"><path d="M7 1 L2 5.5 L7 10" stroke="#fff" stroke-width="2.4" fill="none"/></svg></span><span><svg width="9" height="11"><path d="M2 1 L7 5.5 L2 10" stroke="#fff" stroke-width="2.4" fill="none"/></svg></span></div>
    <div class="pageno">3</div>
  </section>

  <section class="slide s4" aria-label="Table slide">
    <h2 class="heading"><span class="red">Table</span> Presentation</h2>
    <table class="grid">
      <colgroup><col style="width:220px"><col style="width:111px"><col style="width:111px"></colgroup>
      <thead><tr><th class="cat">CATEGORY</th><th class="o1">OPTION 1</th><th class="o2">OPTION 2</th></tr></thead>
      <tbody>
        <tr class="group"><td colspan="3">Category 1</td></tr>
        <tr><td class="item">Lorem ipsum dolor sit amet</td><td class="yes">Yes</td><td class="no">-</td></tr>
        <tr><td class="item">Lorem ipsum dolor sit amet</td><td class="yes">Yes</td><td class="no">-</td></tr>
        <tr><td class="item">Lorem ipsum dolor sit amet</td><td class="yes">Yes</td><td class="no">-</td></tr>
        <tr class="group"><td colspan="3">Category 2</td></tr>
        <tr><td class="item">Lorem ipsum dolor sit amet</td><td class="yes">Yes</td><td class="no">-</td></tr>
        <tr><td class="item">Lorem ipsum dolor sit amet</td><td class="yes">Yes</td><td class="no">-</td></tr>
        <tr><td class="item">Lorem ipsum dolor sit amet</td><td class="yes">Yes</td><td class="no">-</td></tr>
        <tr><td class="item">Lorem ipsum dolor sit amet</td><td class="yes">Yes</td><td class="no">-</td></tr>
        <tr class="group"><td colspan="3">Category 3</td></tr>
        <tr><td class="item">Lorem ipsum dolor sit amet</td><td class="yes">Yes</td><td class="no">-</td></tr>
        <tr><td class="item">Lorem ipsum dolor sit amet</td><td class="yes">Yes</td><td class="no">-</td></tr>
      </tbody>
    </table>
    <div class="footer"><div class="footer-rule"></div><div class="brand">Brass Lantern Guild</div></div>
    <div class="nav"><span><svg width="9" height="11"><path d="M7 1 L2 5.5 L7 10" stroke="#fff" stroke-width="2.4" fill="none"/></svg></span><span><svg width="9" height="11"><path d="M2 1 L7 5.5 L2 10" stroke="#fff" stroke-width="2.4" fill="none"/></svg></span></div>
    <div class="pageno">4</div>
  </section>

  <section class="slide s5" aria-label="Contact slide">
    <h2 class="heading"><span class="red">Contact</span> Info</h2>
    <div class="map" role="img" aria-label="Map of the office region"></div>
    <div class="contact">
      <p><b class="red">Lorem ipsum</b> dolor sit amet, consectetuer adipiscing elit. Maecenas porttitor congue massa. Fusce posuere, magna sed pulvinar ultricies, purus lectus malesuada libero, sit amet commodo magna eros quis urna.</p>
      <h4>Address</h4>
      <div>48 Harbor Lane<br>Portside, Northland<br>24810 (N.L.)</div>
      <h4>Phone</h4><div>0987-654-321</div>
      <h4>FAX</h4><div>0987-654-321</div>
      <h4>Email</h4><div>info@brasslantern.org</div>
      <h4>Website</h4><div>www.brasslantern.org</div>
    </div>
    <div class="social"><i></i><i></i><i></i><i></i><span>@BRASS<span class="red" style="margin:0">LANTERN</span></span></div>
    <div class="footer"><div class="footer-rule"></div><div class="brand">Brass Lantern Guild</div></div>
    <div class="nav"><span><svg width="9" height="11"><path d="M7 1 L2 5.5 L7 10" stroke="#fff" stroke-width="2.4" fill="none"/></svg></span><span><svg width="9" height="11"><path d="M2 1 L7 5.5 L2 10" stroke="#fff" stroke-width="2.4" fill="none"/></svg></span></div>
    <div class="pageno">5</div>
  </section>

  <section class="slide s6" aria-label="Closing slide">
    <div class="rule" style="top:61px"></div>
    <h2 class="thanks"><span class="red">Thank</span>You</h2>
    <div class="rule" style="top:195px"></div>
    <div class="end-brand"><span class="dot"></span>Brass Lantern Guild</div>
    <div class="band"></div>
  </section>

</main>
</body>
</html>
```